Redesign of General Contractor Website

I currently have a wordpress site that needs some work. I would like to revitalize what we currently have to look more modern and up-to-date.
I want to be able to easily post pictures from new jobs and have a link to my own blog (not yet online). My current website can be found at www.brovikbuilders.com
the attached pictures are a site I built in Muse. i really like that sort of theme.
PLEASE NOTE: I am not interested in completely remaking the site, simply adding more functionalty and spicing it up a bit. (more animation, interactive elements, layering, etc...)
Target Market(s)
Property owners, Home owners, business owners, property managers, Decision makers purchasing a construction project, specifically Remodels, renovations, or damage restoration, with some or limited knowledge about how to complete one of those projects.
Industry/Entity Type
Contractor
Coding
Coded - Design and coding required
Number of Pages Required
1 page
Requirements
Must have
- Updateable photo bank displaying pictures from recent jobs that we can easily change and update. An embedded youtube pane showing our most recent video via our youtube channel. Animation and/or transition effects. The small circular logos must stay (I would like to see these be used with animation/transitional effects.
- Must be consistent with other marketing material. This can be found on our facebook page or in the power point file attached.
- Must use colors and fonts found at www.brovikbuilders.com
Nice to have
- Stock photos available if needed.
Should not have
- changes in logo design or re wording of text (use lorim ipsum if needed)
- No multiple pages, redesigning fonts

```html
<!DOCTYPE html>
<html lang="en">
<head>
<meta charset="utf-8">
<title>Brovik Builders</title>
<link href="https://fonts.googleapis.com/css2?family=Open+Sans:wght@400;600;700;800&display=swap" rel="stylesheet">
<style>
:root{
  --orange:#e8561f;
  --navy:#1d2a63;
  --band:#2e4393;
  --band-dark:#1f2f72;
  --ink:#333;
  --muted:#666;
  --light:#f1f1f1;
  --line:#d8d8d8;
  --footer:#2b2b2b;
  --footer-dark:#1f1f1f;
  --white:#fff;
}
*{box-sizing:border-box;margin:0;padding:0}
html,body{width:1200px;height:4800px;overflow:hidden}
body{font-family:"Open Sans",Arial,sans-serif;color:var(--ink);background:var(--white);font-size:13px;line-height:1.6}
section,header,footer{position:relative;width:1200px}
.center{text-align:center}
.section-title{font-weight:700;font-size:40px;color:var(--orange);letter-spacing:1px;text-transform:uppercase;text-align:center}
.body-copy{width:1040px;margin:0 auto;text-align:center;font-size:12px;color:var(--muted)}
.btn{display:inline-block;background:var(--navy);color:var(--white);font-weight:700;font-size:17px;padding:8px 30px;letter-spacing:1px}

/* hero */
.hero{height:576px;background:linear-gradient(180deg,#2c4a78 0%,#5a6f8c 45%,#8a6a4a 75%,#3b3a35 100%);overflow:hidden}
.hero .arrow{position:absolute;top:270px;width:24px;height:24px}
.hero .arrow.left{left:14px}.hero .arrow.right{right:14px}
.brand-badge{position:absolute;left:504px;top:192px;width:192px;height:192px;border-radius:50%;background:var(--white);display:flex;align-items:center;justify-content:center;flex-direction:column}
.brand-badge .name{font-weight:800;font-size:30px;color:var(--navy);line-height:1.05;text-align:center}

/* nav */
.nav{height:42px;background:#ececec;display:flex;justify-content:center;align-items:center;gap:34px;font-size:12px;font-weight:600;color:#444}

/* mission */
.mission{height:614px;padding-top:56px}
.mission .body-copy{margin-top:18px}
.badges{display:flex;justify-content:center;gap:40px;margin-top:28px;align-items:center}
.badge{background:#e6e9f0;border:1px solid #c8cdd9}
.video{width:400px;height:226px;margin:40px auto 0;background:linear-gradient(180deg,#8fa3bf,#4a5664);position:relative}
.video .play{position:absolute;left:170px;top:88px;width:60px;height:42px;background:#d9261c;border-radius:10px}
.video .play:after{content:"";position:absolute;left:24px;top:12px;border-left:16px solid #fff;border-top:9px solid transparent;border-bottom:9px solid transparent}

/* hail band */
.hail{height:240px;background:linear-gradient(180deg,var(--band),var(--band-dark));color:var(--white);text-align:center;padding-top:78px}
.hail h2{font-size:38px;font-weight:700;letter-spacing:.5px}
.hail p{font-size:20px;margin-top:2px}
.band-arrow{position:absolute;top:110px;width:22px;height:22px}

/* intro */
.intro{height:352px;padding-top:72px;text-align:center}
.intro .lead{font-size:15px;color:#444;margin-top:20px}
.intro h3{font-size:20px;font-weight:700;color:var(--navy);margin-top:26px}
.intro .btn{margin-top:10px}

/* services */
.services{height:704px;border-top:1px solid var(--line);padding-top:64px}
.services .body-copy{margin-top:12px}
.service-grid{display:grid;grid-template-columns:repeat(5,180px);justify-content:center;column-gap:30px;row-gap:44px;margin-top:46px}
.service{text-align:center}
.service .dot{width:118px;height:118px;border-radius:50%;background:var(--orange);margin:0 auto;display:flex;align-items:center;justify-content:center}
.service .label{font-weight:800;font-size:17px;margin-top:12px;color:#222}

/* about */
.about{height:342px;background:linear-gradient(180deg,var(--band),var(--band-dark));color:#e8ecf8;text-align:center;padding-top:22px}
.about h2{font-size:38px;font-weight:700;color:var(--white);letter-spacing:1px}
.about p{width:1060px;margin:8px auto 0;font-size:12px}

/* team */
.team{height:576px;background:#f3f3f3;padding-top:62px}
.team .section-title{color:var(--navy)}
.members{display:flex;justify-content:center;gap:80px;margin-top:36px}
.member{width:500px;text-align:center}
.member .photo{width:120px;height:120px;border-radius:50%;background:linear-gradient(180deg,#b9b9b9,#7d7d7d);margin:0 auto}
.member .name{font-weight:700;font-size:16px;margin-top:12px}
.member .role{font-size:11px;color:var(--muted)}
.member p{text-align:left;font-size:12px;color:var(--muted);margin-top:12px}
.member .mail{margin-top:14px}

/* guide */
.guide{height:784px;padding-top:50px}
.accordion{width:1000px;margin:30px auto 0}
.acc-head{background:#ececec;border:1px solid var(--line);height:48px;display:flex;align-items:center;padding-left:18px;font-weight:700;font-size:14px;color:#333;margin-bottom:8px;gap:12px}
.acc-body{border:1px solid var(--line);border-top:none;padding:12px 36px 16px;margin:-8px 0 8px;font-size:10.5px;color:var(--muted)}
.acc-body h4{color:var(--orange);font-size:16px;font-weight:600;margin-top:10px}
.acc-body h5{font-size:13px;font-weight:600;color:#333;margin-bottom:6px}
.acc-body p{margin-bottom:8px}

/* cta */
.cta{height:192px;padding-top:32px;text-align:center}
.cta h3{font-size:20px;font-weight:700;color:var(--navy)}
.cta .btn{margin-top:6px}

/* footer */
.site-footer{height:256px;background:var(--footer);color:#ccc;display:flex;gap:60px;padding:32px 100px 0}
.site-footer h4{color:var(--orange);font-size:14px;font-weight:700;margin-bottom:12px}
.contact-form{width:500px;display:grid;grid-template-columns:1fr 1fr;gap:14px 18px}
.contact-form .field{background:var(--white);height:30px;color:#777;font-size:11px;padding:6px 8px}
.contact-form .message{height:44px}
.contact-form .submit{background:var(--orange);color:var(--white);font-weight:700;font-size:11px;display:flex;align-items:center;justify-content:center;width:70px;height:44px}
.links ul{list-style:none;font-size:11px;line-height:1.95}
.info div{font-size:11px;display:flex;gap:8px;align-items:center;margin-bottom:8px}
.bottom-bar{height:64px;background:var(--footer-dark);display:flex;align-items:center;justify-content:space-between;padding:0 100px;color:#888;font-size:10px}
.social{display:flex;gap:8px}
.social span{width:22px;height:22px;border-radius:50%;background:#555;display:block}
</style>
</head>
<body>

<header class="hero">
  <div role="img" aria-label="Evening photo of a large suburban home with lit windows" style="position:absolute;inset:0"></div>
  <svg class="arrow left" viewBox="0 0 24 24"><path d="M16 3 L6 12 L16 21" fill="none" stroke="#fff" stroke-width="3"/></svg>
  <svg class="arrow right" viewBox="0 0 24 24"><path d="M8 3 L18 12 L8 21" fill="none" stroke="#fff" stroke-width="3"/></svg>
  <div class="brand-badge"><span class="name">BROVIK<br>BUILDERS</span></div>
</header>

<nav class="nav"><span>HOME</span><span>WORK</span><span>SERVICES</span><span>ABOUT</span><span>CONTACT</span></nav>

<section class="mission">
  <h2 class="section-title">Mission</h2>
  <p class="body-copy">Brovik Builders takes a Lifetime Relationship approach to solving all your client's construction needs. We believe in leveraging our knowledge with our network to deliver optimal value for our client's properties. Our team of experts works hard to ensure that you receive the highest quality craftsmanship and customer service. Headquartered in Texas, Brovik Builders regularly does business with the area's insurance companies, real estate agencies, and property managers. Our extensive relationships with these companies are built on rapid response times and a top quality customer experience.</p>
  <div class="badges">
    <div class="badge" style="width:170px;height:80px"></div>
    <div class="badge" style="width:88px;height:88px;border-radius:50%"></div>
    <div class="badge" style="width:130px;height:46px"></div>
  </div>
  <div class="video" role="img" aria-label="Embedded company video thumbnail"><span class="play"></span></div>
</section>

<section class="hail">
  <svg class="band-arrow" style="left:14px" viewBox="0 0 24 24"><path d="M16 3 L6 12 L16 21" fill="none" stroke="#fff" stroke-width="3"/></svg>
  <svg class="band-arrow" style="right:14px" viewBox="0 0 24 24"><path d="M8 3 L18 12 L8 21" fill="none" stroke="#fff" stroke-width="3"/></svg>
  <h2>HAS YOUR HOME BEEN THROUGH HAIL AND BACK?</h2>
  <p>Call us Today for your no obligation quote. (555) 010-4271</p>
</section>

<section class="intro">
  <p class="body-copy">It's easy to tell a client what we can do, but we typically let our portfolio and testimonials speak for themselves. Below you will find the most recent projects we completed for very satisfied home owners. It also helps that we have an A+ rating with the Regional Trade Bureau.</p>
  <p class="lead">Please take a moment to view our services and if you have any questions please don't hesitate to call or email us using the form below</p>
  <h3>WHAT CAN BROVIK BUILDERS DO FOR YOU?</h3>
  <span class="btn">CONTACT US</span>
</section>

<section class="services">
  <h2 class="section-title">Services</h2>
  <p class="body-copy">Brovik Builders provides professional services for our customers' homes. We work with you to assess your specific needs and guarantee you a custom solution.</p>
  <p class="body-copy" style="margin-top:10px">Although we specialize in insurance claims, our experts offer a wide range of services with customized service to ensure you get exactly what you need when you need it. In addition to roof repair and installation we offer a preventive maintenance program entitled the Roof Quality Preservation Program. This program includes roof and gutter cleaning as well as a complimentary inspection for any roof or gutter damage. Below you will find an assortment of services we offer homeowners.</p>
  <div class="service-grid">
    <div class="service"><div class="dot"><svg width="60" height="60" viewBox="0 0 60 60"><path d="M6 36 L30 14 L54 36" fill="none" stroke="#fff" stroke-width="7"/></svg></div><div class="label">ROOFING</div></div>
    <div class="service"><div class="dot"><svg width="60" height="60" viewBox="0 0 60 60"><g stroke="#fff" stroke-width="4"><path d="M10 14H50M10 24H50M10 34H50M10 44H50"/></g></svg></div><div class="label">SIDING</div></div>
    <div class="service"><div class="dot"><svg width="60" height="60" viewBox="0 0 60 60"><path d="M10 14H50V24H38V48H28V24H10Z" fill="#fff"/></svg></div><div class="label">GUTTERS</div></div>
    <div class="service"><div class="dot"><svg width="60" height="60" viewBox="0 0 60 60"><rect x="12" y="10" width="36" height="40" fill="none" stroke="#fff" stroke-width="4"/><path d="M30 10V50M12 30H48" stroke="#fff" stroke-width="4"/></svg></div><div class="label">WINDOWS</div></div>
    <div class="service"><div class="dot"><svg width="60" height="60" viewBox="0 0 60 60"><path d="M8 38 L40 16 L52 24 L20 46Z" fill="#fff"/></svg></div><div class="label">DRYWALL</div></div>
    <div class="service"><div class="dot"><svg width="60" height="60" viewBox="0 0 60 60"><g fill="#fff"><path d="M10 20l5-6 5 6v28H10zM25 20l5-6 5 6v28H25zM40 20l5-6 5 6v28H40z"/></g></svg></div><div class="label">FENCES</div></div>
    <div class="service"><div class="dot"><svg width="60" height="60" viewBox="0 0 60 60"><rect x="10" y="10" width="36" height="14" fill="#fff"/><path d="M46 17H52V30H30V40" fill="none" stroke="#fff" stroke-width="3"/><rect x="26" y="40" width="8" height="14" fill="#fff"/></svg></div><div class="label">PAINTING</div></div>
    <div class="service"><div class="dot"><svg width="60" height="60" viewBox="0 0 60 60"><path d="M14 30 L30 16 L46 30 V48 H14Z" fill="none" stroke="#fff" stroke-width="4"/><rect x="26" y="36" width="8" height="12" fill="#fff"/></svg></div><div class="label">CONSULTING</div></div>
    <div class="service"><div class="dot"><svg width="60" height="60" viewBox="0 0 60 60"><path d="M8 30 L30 12 L52 30 V50 H8Z" fill="#fff"/><path d="M14 36H46M14 43H46" stroke="#e8561f" stroke-width="3"/></svg></div><div class="label">METAL BUILDINGS</div></div>
    <div class="service"><div class="dot"><svg width="60" height="60" viewBox="0 0 60 60"><g fill="#fff"><rect x="8" y="14" width="20" height="8"/><rect x="32" y="14" width="20" height="8"/><rect x="8" y="26" width="10" height="8"/><rect x="22" y="26" width="20" height="8"/><rect x="46" y="26" width="6" height="8"/><rect x="8" y="38" width="20" height="8"/><rect x="32" y="38" width="20" height="8"/></g></svg></div><div class="label">RETAINING WALLS</div></div>
  </div>
</section>

<section class="about">
  <h2>ABOUT</h2>
  <p>Brovik Builders takes a customer oriented approach to solving all of our client's needs. Realizing that no two projects are ever the same, Brovik Builders uses forward thinking techniques to satisfy our customers. While most contracting companies use construction methods that are over half of a century old, Brovik Builders sets the bar in innovative thinking. With our team of certified adjusters, we work hand in hand with our customers to provide unprecedented customer service and the utmost efficiency.</p>
  <p style="margin-top:18px">Based out of Hollis County, Brovik Builders does business with the area's insurance companies, real estate agencies, and property managers on a regular basis. Our extensive dealings with these companies have resulted in unprecedented response times, and a fast, worry free experience for our customers. Brovik Builders also carries an "A" rating with the bureau. We provide exceptional customer service, unsurpassed construction quality, and efficiency to ensure our clients receive the highest quality services in the metroplex, without delay.</p>
  <p style="margin-top:18px">The Brovik Builders Team has roots in Hollis County dating back over 100 years. Unlike other contractors, we offer our clients a personalized experience along with the peace of mind that we are ALWAYS just a phone call away!</p>
</section>

<section class="team">
  <h2 class="section-title">The Team</h2>
  <div class="members">
    <div class="member">
      <div class="photo" role="img" aria-label="Portrait of Dana Brovik"></div>
      <div class="name">DANA BROVIK</div><div class="role">Owner</div>
      <p>With a construction background and marketing degree from State University as his foundation, Dana started Brovik Builders in 2011. Dana's vision was to develop the most dependable, customer service oriented construction company in the greater metro area. Combining today's latest technology with proven business practices, Brovik Builders proudly delivers more value to our customers than ANY competitor in our service area and will continue looking to the future for more opportunities to better serve you.</p>
      <svg class="mail" width="22" height="16" viewBox="0 0 22 16"><rect x="1" y="1" width="20" height="14" fill="none" stroke="#555" stroke-width="1.5"/><path d="M1 1 L11 9 L21 1" fill="none" stroke="#555" stroke-width="1.5"/></svg>
    </div>
    <div class="member">
      <div class="photo" role="img" aria-label="Portrait of Marco Brovik"></div>
      <div class="name">MARCO BROVIK</div><div class="role">Manager</div>
      <p>Marco oversees internal operations, account management, and web development for Brovik Builders. Pellentesque convallis molestie enim sit amet efficitur. Etiam id imperdiet lectus. Vivamus lacus justo, ultrices nec erat in, euismod iaculis mauris. Vivamus eleifend vitae nulla vel malesuada. In ac malesuada lacus, et consectetur ante. Fusce vitae lectus sit amet mi pulvinar maximus. Aenean placerat, nibh vel accumsan aliquet, magna nibh accumsan nibh, at tempus nunc ipsum ac tellus.</p>
      <svg class="mail" width="22" height="16" viewBox="0 0 22 16"><rect x="1" y="1" width="20" height="14" fill="none" stroke="#555" stroke-width="1.5"/><path d="M1 1 L11 9 L21 1" fill="none" stroke="#555" stroke-width="1.5"/></svg>
    </div>
  </div>
</section>

<section class="guide">
  <h2 class="section-title" style="font-size:34px">A Step-by-Step Guide to Successful Home Repair</h2>
  <div class="accordion">
    <div class="acc-head"><svg width="10" height="8" viewBox="0 0 10 8"><path d="M0 0H10L5 8Z" fill="#444"/></svg>THE INSPECTION PROCESS</div>
    <div class="acc-body">
      <h4>Step 1: Inspection</h4>
      <h5>A Construction Consultant will inspect your property for signs of damage.</h5>
      <p>We use the same inspection and estimating software as most insurance providers. An inspection from Brovik Builders includes site visits and photographs by a friendly and knowledgeable Construction Consultant. The site visit and photographs are documented and included in the Findings Report.</p>
      <h4>Step 2: Findings Report and Letter of Intent</h4>
      <h5>The Construction Consultant will notify you of his findings.</h5>
      <p>After the initial inspection, our Construction Consultant will notify you of any damage discovered and give you a personalized Findings Report.</p>
      <p>If extensive damage is discovered during the inspection, a Letter of Intent along with a Insurance Claim should promptly be filed.</p>
      <p>The Letter of Intent binds the Customer and Brovik Builders to an agreement allowing Brovik Builders to further inspect, estimate and setup for the project.</p>
      <p>The Letter of Intent includes consideration of $1,750 which will be credited towards the final payment for the restoration project.</p>
      <p>Note: As a homeowner, you have a contractual duty to your insurance company to inspect and take care of your property in order to mitigate unnecessary damages. Once you are aware of damage to your home, Texas insurance policies only allow you 365 days to file a claim or you forfeit your right to obtain payment from the insurance company.</p>
    </div>
    <div class="acc-head"><svg width="8" height="10" viewBox="0 0 8 10"><path d="M0 0L8 5L0 10Z" fill="#444"/></svg>PRE CONSTRUCTION</div>
    <div class="acc-head"><svg width="8" height="10" viewBox="0 0 8 10"><path d="M0 0L8 5L0 10Z" fill="#444"/></svg>PAYMENT INFORMATION</div>
    <div class="acc-head"><svg width="8" height="10" viewBox="0 0 8 10"><path d="M0 0L8 5L0 10Z" fill="#444"/></svg>CONSTRUCTION DAY AND FINAL PAYMENT</div>
    <div class="acc-head"><svg width="8" height="10" viewBox="0 0 8 10"><path d="M0 0L8 5L0 10Z" fill="#444"/></svg>POST CONSTRUCTION</div>
  </div>
</section>

<section class="cta">
  <h3>WANT TO SEE WHAT BROVIK BUILDERS CAN DO FOR YOU?</h3>
  <span class="btn">CONTACT US</span>
</section>

<footer>
  <div class="site-footer">
    <div>
      <h4>CONTACT US</h4>
      <div class="contact-form">
        <div class="field">First name</div><div class="field">Last name</div>
        <div class="field">Email</div><div class="field">Phone</div>
        <div style="display:flex;gap:10px;grid-column:1/3"><div class="field message" style="flex:1">Message</div><div class="submit">SUBMIT</div></div>
      </div>
    </div>
    <div class="links" style="margin-left:80px">
      <h4>LINKS</h4>
      <ul><li>› Home</li><li>› Work</li><li>› Services</li><li>› About</li><li>› Team</li><li>› Guide</li><li>› Contact</li></ul>
    </div>
    <div class="info" style="margin-left:40px">
      <h4>CONTACT INFO</h4>
      <div><svg width="10" height="14" viewBox="0 0 10 14"><path d="M5 0a5 5 0 0 1 5 5c0 4-5 9-5 9S0 9 0 5a5 5 0 0 1 5-5z" fill="#aaa"/></svg>1200 Oak Ridge Rd, Millbrook, TX 76000</div>
      <div><svg width="12" height="12" viewBox="0 0 12 12"><path d="M2 0h3l1 3-2 1a7 7 0 0 0 4 4l1-2 3 1v3c0 1-1 2-2 2A11 11 0 0 1 0 2c0-1 1-2 2-2z" fill="#aaa"/></svg>(555) 010-4271</div>
      <div><svg width="12" height="10" viewBox="0 0 12 10"><rect x=".5" y=".5" width="11" height="9" fill="none" stroke="#aaa"/><path d="M.5 .5L6 5l5.5-4.5" fill="none" stroke="#aaa"/></svg>info@brovikbuilders.com</div>
    </div>
  </div>
  <div class="bottom-bar">
    <span>Copyright © 2017 Brovik Builders - All Rights Reserved</span>
    <div class="social"><span></span><span></span><span></span><span></span><span></span></div>
  </div>
</footer>

</body>
</html>
```